New Website Design & Build Project - Lively Oak Dishes

I am looking for a professional clean looking website design then build of a website for my meal delivery business Lively Oak Dishes. I already have the domain - www.livelyoakdishes.com.au and I will upload brief for the design and layout of the website.

I have a dropbox full of photos, designs, videos and existing graphic design work that I can share with the designers. This can be provided upon designer request.

I am looking to build this site in WORDPRESS and I would like to build the site using the Velmora Page Composer - https://velmoraskins.example/

Target Market(s)

Kids from 2-16 , Teenagers - 16 - 19, Adults - 19 - 80 + - We Cater For Everyone

Industry/Entity Type

Health And Wellness

Coding

Coded - Design and coding required

Number of Pages Required

5+ page

Colors
33b8a4
abd037
ec1f27
fbee3f
3276b5

Requirements
Must have
• Must incorporate the included Lively Oak Dishes & LOD Logo
Must incorporate designs of packaging into website design.
Must keep text styles consistant throughout design
Must be mobile, tablet and desktop view responsive on all devices.
Must be built in Wordpress
The coder must have experience with velmora skins, velmora page composer, velmora prospects and also be very experienced with setting up products using Quillo Storefront plug in-
https://quillostorefront.example/
I want to integrate Postwren - https://dealbarn.example/postwren/ into site as well
Nice to have
• All of the above
Should not have
• No dark colours

```html
<!DOCTYPE html>
<html lang="en">
<head>
<meta charset="utf-8">
<title>Lively Oak Dishes – Home</title>
<link href="https://fonts.googleapis.com/css2?family=Montserrat:wght@400;500;600;700;800&family=Open+Sans:wght@400;600&display=swap" rel="stylesheet">
<style>
:root{
  --green:#58ae2d;
  --green-dark:#4a9a22;
  --red:#cf1820;
  --ink:#1a1a1a;
  --text:#333;
  --muted:#777;
  --panel:#efefef;
  --footer:#222;
  --footer-text:#8a8a8a;
  --white:#fff;
}
*{box-sizing:border-box;margin:0;padding:0}
html,body{width:1200px;height:2878px;overflow:hidden;background:var(--white)}
body{position:relative;font-family:"Open Sans",sans-serif;color:var(--text)}
.abs{position:absolute}
.heading{font-family:"Montserrat",sans-serif;font-weight:800;color:var(--green);text-transform:uppercase;text-align:center}

/* header */
.site-header{position:absolute;left:0;top:0;width:1200px;height:88px;border-bottom:1px solid #ddd}
.brand{position:absolute;left:143px;top:28px;display:flex;align-items:center;gap:10px;font-family:"Montserrat",sans-serif;font-weight:800;font-size:26px;color:var(--ink)}
.brand-mark{width:22px;height:22px;background:var(--green)}
.account-links{position:absolute;right:200px;top:18px;display:flex;gap:11px}
.account-links a{font-family:"Montserrat",sans-serif;font-size:10px;color:var(--green);border:1px solid var(--green);padding:4px 9px;text-decoration:none;text-transform:uppercase}
.cart{position:absolute;left:1018px;top:20px}
.main-nav{position:absolute;left:455px;top:50px;display:flex;gap:29px;font-size:12px}
.main-nav a{color:var(--text);text-decoration:none}
.main-nav a.active{color:var(--green)}

/* hero */
.hero{position:absolute;left:0;top:89px;width:1200px;height:525px;background:radial-gradient(ellipse at 45% 35%,#5a4a3e 0%,#2a2522 45%,#0f0e0d 100%)}
.hero-title{position:absolute;left:268px;top:227px;width:664px;height:67px;background:rgba(20,20,20,.85);font-family:"Montserrat",sans-serif;font-weight:800;font-size:47px;color:var(--red);text-transform:uppercase;display:flex;align-items:center;padding-left:14px}
.hero-arrow{position:absolute;top:241px;width:44px;height:44px;border-radius:50%;background:var(--white);display:flex;align-items:center;justify-content:center}

/* subscription */
.subscribe-title{left:0;top:686px;width:1200px;font-size:33px}
.subscribe-text{left:0;top:740px;width:1200px;text-align:center;font-size:16px;color:var(--ink)}
.btn-dark{position:absolute;left:516px;top:782px;width:168px;height:56px;background:var(--ink);color:var(--white);font-family:"Montserrat",sans-serif;font-weight:600;font-size:24px;display:flex;align-items:center;justify-content:center}

/* products */
.products{position:absolute;left:0;top:917px;width:1200px;height:569px;background:linear-gradient(90deg,#3a2a1e,#1e1a16 40%,#231d17 70%,#4a3422)}
.products-title{left:0;top:72px;width:1200px;font-size:32px}
.product-card{position:absolute;top:127px;width:217px;height:361px;background:var(--white);text-align:center}
.product-photo{height:218px;background:radial-gradient(circle,#c98a52 0%,#b0663a 30%,#f2f2f2 60%)}
.product-dot{position:absolute;top:6px;right:6px;width:18px;height:18px;border-radius:50%;border:3px solid var(--white)}
.product-name{font-family:"Montserrat",sans-serif;font-size:18px;color:var(--ink);margin-top:20px}
.product-plan{font-size:13px;color:var(--ink);margin-top:2px}
.product-price{font-family:"Montserrat",sans-serif;font-size:19px;color:var(--green);margin-top:5px}
.btn-green{display:flex;align-items:center;justify-content:center;background:var(--green);color:var(--white);font-family:"Montserrat",sans-serif;font-weight:600;text-transform:uppercase}
.product-card .btn-green{position:absolute;left:8px;right:8px;bottom:9px;height:33px;font-size:16px}
.carousel-arrow{position:absolute;top:290px}

/* member & blog */
.panel{position:absolute;left:144px;width:912px;height:336px;background:var(--panel)}
.panel-photo{position:absolute;top:0;width:456px;height:336px}
.signup-title{left:0;top:46px;width:456px;font-size:32px}
.signup-text{left:50px;top:99px;width:356px;text-align:center;font-size:13px;line-height:20px}
.field{position:absolute;width:207px;height:40px;background:var(--white);border:1px solid #ccc;font-size:11px;color:var(--muted);padding:12px 16px}
.blog-title{left:456px;top:56px;width:456px;font-size:32px}
.blog-subtitle{left:456px;top:109px;width:456px;text-align:center;font-family:"Montserrat",sans-serif;font-weight:400;font-size:16px;color:var(--ink);text-transform:uppercase}
.blog-text{left:478px;top:137px;width:412px;text-align:center;font-size:11.5px;line-height:21px}

/* contact */
.contact-title{left:0;top:2318px;width:1200px;font-size:32px}
.contact-line{left:0;top:2364px;width:1200px;display:flex;justify-content:center;align-items:center;gap:12px;font-family:"Montserrat",sans-serif;font-size:21px;color:var(--ink)}
.contact-hours{left:0;top:2403px;width:1200px;display:flex;justify-content:center;align-items:center;gap:6px;font-family:"Montserrat",sans-serif;font-size:15px;color:var(--ink)}

/* footer */
.site-footer{position:absolute;left:0;top:2502px;width:1200px;height:376px;background:var(--footer)}
.footer-heading{position:absolute;top:44px;font-family:"Montserrat",sans-serif;font-weight:600;font-size:15px;color:var(--green);text-transform:uppercase}
.footer-text{position:absolute;font-size:11px;line-height:19px;color:var(--footer-text)}
.footer-links{position:absolute;top:74px;list-style:none;font-family:"Montserrat",sans-serif;font-size:11px;line-height:24px;color:var(--footer-text);text-transform:uppercase}
.social-box{position:absolute;top:75px;width:44px;height:44px;border:1px solid #555}
.footer-rule{position:absolute;left:144px;top:263px;width:912px;height:1px;background:#444}
.footer-meta{position:absolute;left:0;width:1200px;text-align:center;font-size:11px;color:var(--footer-text)}
</style>
</head>
<body>

<header class="site-header">
  <div class="brand"><span class="brand-mark"></span>Lively Oak Dishes</div>
  <div class="account-links"><a href="#">Member sign up</a><a href="#">Log in</a></div>
  <svg class="cart" width="38" height="26" viewBox="0 0 38 26" aria-label="Cart">
    <circle cx="9" cy="8" r="7" fill="#58ae2d"/><text x="9" y="11" font-size="8" fill="#fff" text-anchor="middle" font-family="Open Sans">0</text>
    <path d="M16 12h20l-3 12H19z" fill="#1a1a1a"/><path d="M21 12l5-7 5 7" fill="none" stroke="#1a1a1a" stroke-width="2"/>
  </svg>
  <nav class="main-nav">
    <a class="active" href="#">Bulking &amp; Muscle Gain</a><a href="#">Weightloss</a><a href="#">Kids Meals</a><a href="#">Vegan</a><a href="#">Beverages</a><a href="#">Specials</a><a href="#">Supplements</a>
  </nav>
</header>

<section class="hero" role="img" aria-label="Athlete resting in a dim gym beside a shaker bottle and protein scoop">
  <div class="hero-arrow" style="left:55px"><svg width="18" height="18" viewBox="0 0 18 18"><path d="M12 2L5 9l7 7" fill="none" stroke="#111" stroke-width="3"/></svg></div>
  <div class="hero-title">Bulking &amp; Muscle Gain</div>
  <div class="hero-arrow" style="left:1099px"><svg width="18" height="18" viewBox="0 0 18 18"><path d="M6 2l7 7-7 7" fill="none" stroke="#111" stroke-width="3"/></svg></div>
</section>

<h2 class="heading abs subscribe-title">Lively Oak Dishes Subscription Service</h2>
<p class="abs subscribe-text">Join the Lively Oak Dishes subscription service to get the lowest prices. Cancel anytime.</p>
<a class="btn-dark">JOIN NOW</a>

<section class="products">
  <h2 class="heading abs products-title">Our Products</h2>
  <svg class="carousel-arrow" style="left:55px" width="18" height="30" viewBox="0 0 18 30"><path d="M15 3L4 15l11 12" fill="none" stroke="#fff" stroke-width="3"/></svg>
  <div class="product-card" style="left:144px"><div class="product-photo" role="img" aria-label="Plate of mixed vegetables and corn"></div><span class="product-dot" style="background:#1f8a3a"></span><div class="product-name">LOD Kids</div><div class="product-plan">7 Day Meal Plan</div><div class="product-price">$35</div><a class="btn-green">Join now</a></div>
  <div class="product-card" style="left:375px"><div class="product-photo" role="img" aria-label="Sliced roast with carrots and broccoli"></div><span class="product-dot" style="background:#8a0b14"></span><div class="product-name">LOD Adult</div><div class="product-plan">7 Day Meal Plan</div><div class="product-price">$54</div><a class="btn-green">Join now</a></div>
  <div class="product-card" style="left:606px"><div class="product-photo" role="img" aria-label="Grilled fish with broccoli and beans"></div><span class="product-dot" style="background:#e0ac0a"></span><div class="product-name">LOD Adult</div><div class="product-plan">7 Day Couples Meal Plan</div><div class="product-price">$108</div><a class="btn-green">Join now</a></div>
  <div class="product-card" style="left:837px"><div class="product-photo" role="img" aria-label="Spaghetti with meat sauce and cheese"></div><span class="product-dot" style="background:#1c5fb0"></span><div class="product-name">LOD Adult</div><div class="product-plan">21 Meals Per Week Plan</div><div class="product-price">$162</div><a class="btn-green">Join now</a></div>
  <svg class="carousel-arrow" style="left:1126px" width="18" height="30" viewBox="0 0 18 30"><path d="M3 3l11 12L3 27" fill="none" stroke="#fff" stroke-width="3"/></svg>
</section>

<section class="panel" style="top:1566px">
  <h2 class="heading abs signup-title">Member Sign Up</h2>
  <p class="abs signup-text">Vivamus eleifend vitae nulla vel malesuada. In ac malesuada lacus, et consectetur ante.</p>
  <div class="field" style="left:16px;top:147px">Create Account</div>
  <div class="field" style="left:232px;top:147px">Full Name</div>
  <div class="field" style="left:16px;top:195px">Mobile Number</div>
  <div class="field" style="left:232px;top:195px">Email</div>
  <a class="btn-green abs" style="left:16px;top:243px;width:423px;height:40px;font-size:16px">Join now</a>
  <div class="panel-photo" style="left:456px;background:linear-gradient(160deg,#dfe4ea,#b9c2cc 55%,#d6b48c)" role="img" aria-label="Man at a desk using a tablet beside a laptop"></div>
</section>

<section class="panel" style="top:1910px">
  <div class="panel-photo" style="left:0;background:linear-gradient(90deg,#e9ebec,#d9d9d9 60%,#c9c9c9)" role="img" aria-label="Woman holding a glass of green smoothie"></div>
  <h2 class="heading abs blog-title">Lively Life Blog</h2>
  <h3 class="abs blog-subtitle">The best green smoothie to start your day</h3>
  <p class="abs blog-text">The King of Green Smoothies would have to be my Superfood Green Smoothie which contains all the elements necessary for unbelievable muscle growth!!! In order to strip off the fat, add lean muscle mass &amp; to provide your body with all the best vitamins &amp; minerals try the following recipe.</p>
  <a class="btn-green abs" style="left:620px;top:235px;width:128px;height:40px;font-size:16px">Read more</a>
</section>

<h2 class="heading abs contact-title">Contact Us</h2>
<div class="abs contact-line">
  <svg width="16" height="16" viewBox="0 0 16 16"><path d="M3 1l3 3-2 2c1 2 3 4 5 5l2-2 3 3-2 3C7 15 1 9 1 3z" fill="#1a1a1a"/></svg>
  <span>0400 118 276</span><span>|</span>
  <svg width="20" height="15" viewBox="0 0 20 15"><rect width="20" height="15" rx="1" fill="#1a1a1a"/><path d="M1 1l9 7 9-7" fill="none" stroke="#fff" stroke-width="1.5"/></svg>
  <span>hello@livelyoakdishes.com.au</span>
</div>
<div class="abs contact-hours">
  <svg width="12" height="12" viewBox="0 0 12 12"><circle cx="6" cy="6" r="5" fill="none" stroke="#1a1a1a" stroke-width="1.5"/><path d="M6 3v3h2" fill="none" stroke="#1a1a1a" stroke-width="1.5"/></svg>
  <span>Opening Hours – Mon- Friday – 9 – 5 pm &nbsp;|&nbsp; Sat – 8 am – 12 pm</span>
</div>

<footer class="site-footer">
  <h4 class="footer-heading" style="left:143px">Newsletter Signup</h4>
  <p class="footer-text" style="left:144px;top:72px">Fusce vitae lectus sit amet mi pulvinar maximus.<br>Aenean placerat, nibh vel accumsan aliquet</p>
  <div class="abs" style="left:144px;top:124px;width:250px;height:40px;background:#fff;font-size:11px;color:#555;padding:13px 15px">Email Address</div>
  <a class="btn-green abs" style="left:144px;top:172px;width:122px;height:35px;font-size:16px;font-weight:500">Subscribe</a>
  <div class="abs" style="left:300px;top:180px;display:flex;align-items:center;gap:6px;font-family:'Montserrat',sans-serif;font-size:17px;color:#aaa"><span style="width:14px;height:14px;background:#aaa;display:block"></span>Postwren</div>

  <h4 class="footer-heading" style="left:523px">Links</h4>
  <ul class="footer-links" style="left:525px"><li>Bulking &amp; Muscle Gain</li><li>Weightloss</li><li>Kids Meals</li><li>Vegan</li><li>Beverages</li><li>Specials</li></ul>
  <ul class="footer-links" style="left:683px"><li>Supplements</li><li>Disclaimer</li><li>Terms &amp; Conditions</li><li>Privacy – Policy</li></ul>

  <h4 class="footer-heading" style="left:931px">Follow us on</h4>
  <div class="social-box" style="left:932px" aria-label="Social profile"></div>
  <div class="social-box" style="left:996px" aria-label="Social profile"></div>

  <div class="footer-rule"></div>
  <p class="footer-meta" style="top:299px">Copyright © 2020 – Lively Oak Dishes Pty Ltd – ABN – 00 000 000 000.</p>
  <p class="footer-meta" style="top:328px">
    <svg width="9" height="11" viewBox="0 0 9 11" style="vertical-align:-1px"><path d="M4.5 0A4 4 0 0 0 .5 4c0 3 4 7 4 7s4-4 4-7a4 4 0 0 0-4-4z" fill="#8a8a8a"/></svg>
    Shop 4 – 28 Harbour Lane, Brookfield, QLD, 4000
  </p>
</footer>

</body>
</html>
```